BOLD & MINIMALIST DESIGN NEEDED

We want a very bold but minimalistic business card design that is impactful and utilizes both sides of the business card. Our current logo is included for your use.

We want bold fonts and good use of negative space. We don't want the logo to overpower the design.

Target Market(s)

Professionals who are building new commercial buildings.

Industry/Entity Type

Construction

Contact Information for Business Card

Name, Title, email, office phone, cell phone, website

Font styles to use
Serif
Sans Serif

Requirements
Must have
• Bold design!

```html
<!DOCTYPE html>
<html lang="en">
<head>
<meta charset="utf-8">
<title>Ridgeline Design + Build — Business Card</title>
<link rel="stylesheet" href="https://fonts.googleapis.com/css2?family=Montserrat:wght@400;500;700;800&display=swap">
<style>
  :root {
    --ink: #1e1e1e;
    --paper: #ffffff;
    --green: #7ac143;
    --grey-text: #3a3a3a;
    --backdrop: #d4d4d4;
    --card-w: 540px;
    --card-h: 309px;
    --radius: 18px;
  }
  * { box-sizing: border-box; margin: 0; padding: 0; }
  html, body {
    width: 1200px; height: 802px; overflow: hidden;
    background: var(--backdrop);
    font-family: "Montserrat", sans-serif;
  }
  .sheet {
    width: 1200px; height: 802px;
    display: flex; align-items: center; justify-content: center; gap: 40px;
  }
  .card {
    position: relative;
    width: var(--card-w); height: var(--card-h);
    border-radius: var(--radius);
    overflow: hidden;
    box-shadow: 0 10px 24px rgba(0,0,0,.28);
  }
  /* front */
  .card--front { background: var(--paper); color: var(--ink); }
  .front-band { position: absolute; inset: 0; }
  .brand {
    position: absolute; left: 34px; top: 62px;
  }
  .brand__name {
    font-weight: 800; font-size: 38px; line-height: 1; letter-spacing: -.5px;
    padding-bottom: 4px; border-bottom: 2px solid var(--ink);
  }
  .brand__tag {
    font-weight: 500; font-size: 12px; letter-spacing: 6.5px; margin-top: 4px;
    padding-left: 30px;
  }
  .person { position: absolute; left: 34px; top: 160px; }
  .person__name { color: var(--green); font-weight: 800; font-size: 25px; letter-spacing: .5px; }
  .person__title { color: var(--grey-text); font-weight: 500; font-size: 15px; margin-top: 2px; }
  .contacts { list-style: none; margin-top: 14px; }
  .contacts li {
    display: flex; align-items: center; gap: 8px;
    font-size: 14px; font-weight: 500; color: var(--grey-text); line-height: 1.45;
  }
  .contacts svg { width: 12px; height: 12px; flex: none; }
  .mark-square {
    position: absolute; right: 46px; top: 34px;
    width: 96px; height: 96px; background: var(--green);
  }
  /* back */
  .card--back {
    background: var(--ink); color: var(--paper);
    display: flex; align-items: center; justify-content: center;
  }
  .back-brand { display: flex; align-items: center; gap: 16px; }
  .back-brand__square { width: 44px; height: 44px; background: var(--green); }
  .back-brand__name {
    font-weight: 800; font-size: 50px; line-height: 1; letter-spacing: -.5px;
    padding-bottom: 5px; border-bottom: 2px solid var(--paper);
  }
  .back-brand__tag {
    font-weight: 500; font-size: 15px; letter-spacing: 8px; margin-top: 5px; padding-left: 40px;
  }
</style>
</head>
<body>
<main class="sheet">

  <section class="card card--front" aria-label="Card front">
    <div class="mark-square"></div>
    <svg class="front-band" viewBox="0 0 540 309" aria-hidden="false">
      <path d="M245,309 Q390,150 540,92 L540,309 Z" fill="#1e1e1e"/>
      <path id="web-curve" d="M300,306 Q420,178 535,132" fill="none"/>
      <text font-family="Montserrat, sans-serif" font-size="13" font-weight="500" fill="#ffffff" letter-spacing=".4">
        <textPath href="#web-curve" startOffset="12">www.<tspan fill="#7ac143">ridgelinebuild</tspan>.com</textPath>
      </text>
    </svg>

    <div class="brand">
      <div class="brand__name">RIDGELINE</div>
      <div class="brand__tag">DESIGN + BUILD</div>
    </div>

    <div class="person">
      <div class="person__name">DANA WHITFIELD</div>
      <div class="person__title">Owner/CEO</div>
      <ul class="contacts">
        <li>
          <svg viewBox="0 0 12 12"><path d="M2.5 1h2l1 2.6-1.3.9a6 6 0 0 0 3.3 3.3l.9-1.3 2.6 1v2a1 1 0 0 1-1 1A9.5 9.5 0 0 1 1.5 2a1 1 0 0 1 1-1z" fill="#7ac143"/></svg>
          07 5120 3344
        </li>
        <li>
          <svg viewBox="0 0 12 12"><rect x="3" y=".5" width="6" height="11" rx="1.2" fill="none" stroke="#7ac143" stroke-width="1.3"/><rect x="5" y="9" width="2" height="1" fill="#7ac143"/></svg>
          0427 615 902
        </li>
        <li>
          <svg viewBox="0 0 12 12"><rect x=".5" y="2.5" width="11" height="7.5" fill="#7ac143"/><path d="M.5 2.5 6 7l5.5-4.5" fill="none" stroke="#fff" stroke-width="1"/></svg>
          info@ridgelinebuild.com
        </li>
      </ul>
    </div>
  </section>

  <section class="card card--back" aria-label="Card back">
    <div class="back-brand">
      <div class="back-brand__square"></div>
      <div>
        <div class="back-brand__name">RIDGELINE</div>
        <div class="back-brand__tag">DESIGN + BUILD</div>
      </div>
    </div>
  </section>

</main>
</body>
</html>
```